UK Online Auction Site needs a clever design

We need a contemporary landing page and registration page design for a UK auction website, that look equally at home on PC's and tablets . The design should be fresh, bright, clean, professional, robust, and familiar. We would like to see something clever but functional.

Online

```html
<!DOCTYPE html>
<html lang="en">
<head>
<meta charset="utf-8">
<title>Bidwell – UK Online Auctions</title>
<link rel="stylesheet" href="https://fonts.googleapis.com/css2?family=Open+Sans:wght@400;600;700&family=Open+Sans+Condensed:wght@700&display=swap">
<style>
:root{
  --blue:#12a0e3;
  --blue-dark:#0b86c4;
  --teal:#117fa8;
  --orange:#ee5a12;
  --red:#e53b2a;
  --ink:#222;
  --muted:#555;
  --line:#e3e3e3;
  --panel:#f7f7f7;
  --header:#f3f3f3;
  --footer-dark:#333;
  --footer-band:#f0f0f0;
  --white:#fff;
}
*{box-sizing:border-box;margin:0;padding:0}
html,body{width:721px;height:1200px;overflow:hidden}
body{position:relative;background:var(--white);font-family:"Open Sans",Arial,sans-serif;color:var(--ink)}
.abs{position:absolute}
a{color:inherit;text-decoration:none}

/* top bar */
.topbar{left:0;top:0;width:721px;height:27px;background:var(--blue);color:var(--white);font-size:6.5px;font-weight:600}
.topbar .phone{left:103px;top:0;height:27px;display:flex;align-items:center;gap:8px;font-weight:400;font-size:7px}
.topbar .phone .dot{width:13px;height:13px;border-radius:50%;background:#5a6f7c;display:flex;align-items:center;justify-content:center}
.topbar .menu{top:0;height:27px;display:flex;align-items:center;gap:5px;text-transform:uppercase}

/* header */
.header{left:0;top:27px;width:721px;height:102px;background:var(--header)}
.brand{left:103px;top:46px;height:37px;display:flex;align-items:center;gap:6px;font-size:24px;font-weight:700;color:var(--blue-dark)}
.brand .mark{width:12px;height:12px;background:var(--blue-dark);border-radius:50%}
.cart{left:516px;top:51px;width:98px;height:28px;background:var(--blue);color:var(--white);display:flex;align-items:center;gap:6px;padding-left:6px;border:1px solid #fff;outline:1px solid var(--blue)}
.cart .ico{width:18px;height:18px;background:var(--white);display:flex;align-items:center;justify-content:center}
.cart .t1{font-size:7.5px;line-height:1.2}
.cart .t2{font-size:4.5px}

/* search row */
.shopcat{left:103px;top:104px;width:130px;height:25px;background:var(--blue);color:var(--white);font-size:8px;display:flex;align-items:center;justify-content:space-between;padding:0 9px}
.shopcat .chev{width:10px;height:10px;border-radius:50%;background:var(--white);display:flex;align-items:center;justify-content:center}
.search{left:249px;top:104px;width:369px;height:25px;display:flex;background:var(--white);border:1px solid var(--line)}
.search .cat{width:88px;background:var(--blue);color:var(--white);font-size:8px;display:flex;align-items:center;padding-left:10px;gap:10px}
.search .field{flex:1;display:flex;align-items:center;justify-content:flex-end;padding-right:8px}
.search .go{width:28px;background:var(--blue);display:flex;align-items:center;justify-content:center}

/* categories */
.catlist{left:103px;top:129px;width:130px;height:193px;border:1px solid var(--line);border-top:none;list-style:none;background:var(--white)}
.catlist li{height:24px;border-bottom:1px solid #eee;font-size:7px;display:flex;align-items:center;justify-content:space-between;padding:0 10px}
.catlist li:last-child{border-bottom:none}
.catlist li::after{content:"›";color:#aaa;font-size:9px}

/* hero */
.hero{left:249px;top:139px;width:369px;height:183px;background:linear-gradient(135deg,#fff,#ececec);border:1px solid var(--line)}
.hero .off{left:24px;top:10px;font-size:29px;color:var(--blue);font-weight:400}
.hero .copy{left:28px;top:56px;width:118px;text-align:center}
.hero .copy .l1{font-size:13px}
.hero .copy .l2{font-size:24px;color:var(--red);line-height:1.1}
.hero .copy .l3{font-size:9.5px;margin-top:6px}
.hero .cta{left:27px;top:143px;width:69px;height:26px;background:var(--red);color:var(--white);font-size:9px;display:flex;align-items:center;justify-content:center;border-radius:3px}
.hero .dots{left:115px;top:155px;display:flex;gap:4px}
.hero .dots i{width:6px;height:6px;border-radius:50%;background:#333;border:1px solid #ccc}
.hero .dots i:first-child{background:var(--red)}
.hero .product{left:158px;top:28px;width:196px;height:130px;background:radial-gradient(ellipse 60% 55% at 58% 50%,#2a2a2a 0%,#555 45%,rgba(240,240,240,0) 100%)}

/* sign in strip */
.signin{left:102px;top:338px;width:347px;height:135px;background:var(--panel);border:1px solid var(--line)}
.signin .col{top:0;height:100%}
.signin .login{left:0;width:190px;padding:12px 17px}
.signin h3,.signin h4{font-size:9px;font-weight:400}
.signin .note{font-size:6px;line-height:1.7;color:var(--muted);margin-top:12px}
.signin .btn{margin-top:10px;width:102px;height:24px;background:var(--blue);color:var(--white);font-size:10px;display:flex;align-items:center;justify-content:center;border-radius:2px}
.signin .reg{font-size:6px;margin-top:12px}
.signin .reg a{color:var(--blue)}
.signin .trust{left:190px;width:157px;padding:12px 13px;border-left:1px solid var(--line);background:var(--white)}
.signin .row{display:flex;gap:9px;margin-top:10px}
.signin .row svg{flex:none}
.signin .row b{font-size:7px;font-weight:400;display:block}
.signin .row span{font-size:6px;line-height:1.7;color:var(--muted);display:block;margin-top:3px}
.promo{left:458px;top:338px;width:160px;height:135px;border:1px solid var(--line);padding:2px}
.promo .photo{width:100%;height:100%;background:linear-gradient(120deg,#6d6558 0%,#3d4f63 40%,#6d7f90 60%,#25384b);position:relative}
.promo .t1{position:absolute;left:8px;bottom:24px;font-family:"Open Sans Condensed","Arial Narrow",sans-serif;font-weight:700;font-size:19px;color:var(--white)}
.promo .t2{position:absolute;left:8px;bottom:5px;font-family:"Open Sans Condensed","Arial Narrow",sans-serif;font-weight:700;font-size:13px;color:#f4b400}

/* product sections */
.section-head{left:102px;width:516px;height:24px;border-bottom:1px solid #eee;display:flex;justify-content:space-between;align-items:flex-start}
.section-head h2{font-size:11.5px;font-weight:400}
.section-head .nav{display:flex;gap:2px}
.section-head .nav i{width:17px;height:16px;background:var(--teal);color:var(--white);font-style:normal;font-size:8px;display:flex;align-items:center;justify-content:center}
.grid{left:103px;width:515px;display:flex;justify-content:space-between}
.card{width:117px;height:200px;border:1px solid #eee;text-align:center;background:var(--panel)}
.card .img{height:120px;background:var(--white)}
.card .name{font-size:7px;margin-top:10px;white-space:nowrap}
.card .price{font-size:7px;margin-top:10px}
.card .add{margin:8px auto 0;width:56px;height:18px;background:var(--orange);color:var(--white);font-size:7px;display:flex;align-items:center;justify-content:center;border-radius:2px}
.img.camera{background:radial-gradient(ellipse 55% 50% at 50% 52%,#4a4a4a 0%,#a9a9a9 45%,#f6f6f6 90%)}
.img.shades{background:radial-gradient(ellipse 60% 35% at 50% 50%,#5a3e86 0%,#9a8db0 45%,#fbfbfb 90%)}
.img.tee{background:radial-gradient(ellipse 55% 55% at 50% 52%,#d9405a 0%,#e08a98 45%,#efefef 90%)}
.img.model{background:linear-gradient(90deg,#8ea86a 0%,#c9b38f 30%,#4a8fd0 50%,#c9b38f 70%,#9bb07a 100%)}
.img.trainer{background:radial-gradient(ellipse 60% 50% at 50% 55%,#8c8c93 0%,#c2c2c7 45%,#fbfbfb 90%)}
.img.blazer{background:radial-gradient(ellipse 45% 60% at 50% 50%,#1f3fa8 0%,#7b8fcf 50%,#fbfbfb 92%)}
.img.pouch{background:radial-gradient(ellipse 45% 30% at 50% 50%,#222 0%,#8a8a8a 45%,#fbfbfb 90%)}

/* footer */
.foot-band{left:0;top:1021px;width:721px;height:25px;background:var(--footer-band)}
.foot-band h5{position:absolute;top:6px;font-size:9px;font-weight:400}
.foot-band .news{left:458px;color:var(--white);font-size:7px;top:8px}
.foot-dark{left:0;top:1046px;width:721px;height:108px;background:var(--footer-dark);color:#ddd}
.foot-dark ul{position:absolute;top:12px;list-style:none;font-size:6px;line-height:11px}
.foot-dark .email{position:absolute;left:458px;top:14px;width:160px;height:17px;background:var(--white);border:1px solid #ccc;font-size:6.5px;color:#bbb;padding:4px 8px}
.foot-dark .sub{position:absolute;top:42px;width:75px;height:18px;color:var(--white);font-size:7px;font-weight:700;display:flex;align-items:center;justify-content:center;gap:6px}
.foot-dark .social{position:absolute;left:103px;top:69px;display:flex;gap:7px}
.foot-dark .social i{width:17px;height:17px;border-radius:50%;background:radial-gradient(circle at 50% 40%,#fafafa,#cfcfcf);border:2px solid #5a5a5a;box-shadow:0 0 0 1px #888}
.bottom{left:0;top:1154px;width:721px;height:46px;background:var(--white);font-size:7px}
.bottom .brand2{position:absolute;left:104px;top:14px;font-size:14px;font-weight:700;color:var(--blue-dark);display:flex;align-items:center;gap:4px}
.bottom .brand2 i{width:8px;height:8px;border-radius:50%;background:var(--blue-dark)}
.bottom .copy{position:absolute;left:178px;top:19px}
.bottom .links{position:absolute;left:494px;top:19px;font-size:6px}
</style>
</head>
<body>

<header class="abs topbar">
  <div class="abs phone"><span class="dot"><svg width="7" height="7" viewBox="0 0 10 10"><path d="M2 1l2 2-1 1.5c.8 1.6 1.9 2.7 3.5 3.5L8 6l2 2-1.5 1.5C4.5 9 1 5.5.5 1.5z" fill="#fff"/></svg></span>555-010-2030</div>
  <div class="abs menu" style="left:398px">♥ Favourite ⌄</div>
  <div class="abs menu" style="left:472px">▪ Sell ⌄</div>
  <div class="abs menu" style="left:528px">● My Account</div>
  <div class="abs menu" style="left:592px">▪ Login</div>
</header>

<div class="abs header"></div>
<div class="abs brand"><span class="mark"></span>Bidwell</div>
<div class="abs cart">
  <span class="ico"><svg width="12" height="10" viewBox="0 0 12 10"><path d="M0 1h2l2 6h6l2-5H3" fill="none" stroke="#12a0e3" stroke-width="1.4"/><circle cx="5" cy="9" r="1" fill="#12a0e3"/><circle cx="9" cy="9" r="1" fill="#12a0e3"/></svg></span>
  <div><div class="t1">Shopping Cart</div><div class="t2">Now in your cart 0 items</div></div>
</div>

<div class="abs shopcat">SHOP BY CATEGORY <span class="chev"><svg width="6" height="4" viewBox="0 0 6 4"><path d="M0 0l3 4 3-4z" fill="#12a0e3"/></svg></span></div>
<div class="abs search">
  <div class="cat">All categories <span>⌄</span></div>
  <div class="field"><svg width="20" height="9" viewBox="0 0 20 9"><circle cx="4.5" cy="4.5" r="3.5" fill="#ccc"/><path d="M14 3l3 3 3-3" fill="none" stroke="#aaa"/></svg></div>
  <div class="go"><svg width="12" height="12" viewBox="0 0 12 12"><circle cx="5" cy="5" r="3.8" fill="none" stroke="#fff" stroke-width="1.6"/><path d="M8 8l3 3" stroke="#fff" stroke-width="1.8"/></svg></div>
</div>

<ul class="abs catlist">
  <li>All categories</li><li>Fashion</li><li>Home &amp; Garden</li><li>Electricals &amp; Technology</li>
  <li>Collectables &amp; Antiques</li><li>Jewellery &amp; Beauty</li><li>Toys</li><li>Sport &amp; Leisure</li>
</ul>

<section class="abs hero">
  <div class="abs off">40 % OFF</div>
  <div class="abs copy"><div class="l1">The Smartest</div><div class="l2">Cameras</div><div class="l3">Hurryl While Supplies last</div></div>
  <a class="abs cta">SHOP NOW</a>
  <div class="abs dots"><i></i><i></i><i></i><i></i></div>
  <div class="abs product" role="img" aria-label="Black touchscreen digital camera with long zoom lens"></div>
</section>

<section class="abs signin">
  <div class="abs col login">
    <h3>Sign In</h3>
    <p class="note">Sign-in to your account in order to buy, sell or manage your preferences.</p>
    <a class="btn">Sign In</a>
    <p class="reg">Don't have an account? <a>Register ›</a></p>
  </div>
  <div class="abs col trust">
    <h4>Shop with confidence</h4>
    <div class="row">
      <svg width="20" height="22" viewBox="0 0 20 22"><path d="M10 1l8 3v6c0 5-4 9-8 11-4-2-8-6-8-11V4z" fill="none" stroke="#111" stroke-width="2"/><path d="M6 11l3 3 5-6" fill="none" stroke="#111" stroke-width="2"/></svg>
      <div><b>Completely safe</b><span>Bid on or buy items you're watching or searching for</span></div>
    </div>
    <div class="row">
      <svg width="20" height="22" viewBox="0 0 20 22"><path d="M5 1h10v6a5 5 0 01-10 0zM5 3H1c0 4 2 5 4 5M15 3h4c0 4-2 5-4 5M10 12v5M6 21h8l-1-4H7z" fill="#111" stroke="#111"/></svg>
      <div><b>Premium sellers</b><span>Great service and the best delivery when you buy from premium</span></div>
    </div>
  </div>
</section>

<aside class="abs promo">
  <div class="photo" role="img" aria-label="Close-up of a DSLR camera lens held at a person's side">
    <span class="t1">CAMERA DSLR</span><span class="t2">Be Creative. Visualize</span>
  </div>
</aside>

<div class="abs section-head" style="top:490px"><h2>Featured Products</h2><div class="nav"><i>←</i><i>→</i></div></div>
<div class="abs grid" style="top:533px">
  <div class="card"><div class="img camera" role="img" aria-label="Film camera with black lens"></div><div class="name">2010 TOUR STAFF Bag 10"</div><div class="price">$299.99</div><a class="add">Add To Cart</a></div>
  <div class="card"><div class="img shades" role="img" aria-label="Purple sunglasses"></div><div class="name">16GB A Series Pocket Video</div><div class="price">$299.99</div><a class="add">Add To Cart</a></div>
  <div class="card"><div class="img tee" role="img" aria-label="Red printed t-shirt"></div><div class="name">FUSCE ALIQUAM</div><div class="price">$299.99</div><a class="add">Add To Cart</a></div>
  <div class="card"><div class="img model" role="img" aria-label="Model wearing a blue vest top outdoors"></div><div class="name">2010 TOUR STAFF Bag 10"</div><div class="price">$299.99</div><a class="add">Add To Cart</a></div>
</div>

<div class="abs section-head" style="top:750px"><h2>Items from seller stores</h2><div class="nav"><i>←</i><i>→</i></div></div>
<div class="abs grid" style="top:792px">
  <div class="card"><div class="img trainer" role="img" aria-label="Grey high-top trainer"></div><div class="name">Curabitur imperdiet nibh eget</div><div class="price">$299.99</div><a class="add">Add To Cart</a></div>
  <div class="card"><div class="img blazer" role="img" aria-label="Royal blue blazer"></div><div class="name">Grouped Product</div><div class="price">$299.99</div><a class="add">Add To Cart</a></div>
  <div class="card"><div class="img camera" role="img" aria-label="Film camera with black lens"></div><div class="name">FUSCE ALIQUAM</div><div class="price">$299.99</div><a class="add">Add To Cart</a></div>
  <div class="card"><div class="img pouch" role="img" aria-label="Black leather pouch"></div><div class="name">2010 TOUR STAFF Bag 10"</div><div class="price">$299.99</div><a class="add">Add To Cart</a></div>
</div>

<footer>
  <div class="abs foot-band">
    <h5 style="left:104px">Buy</h5><h5 style="left:191px">Buy</h5><h5 style="left:274px">Support</h5><h5 style="left:351px">Support</h5>
    <span class="abs news">Subscribe to our Newsletter</span>
  </div>
  <div class="abs foot-dark">
    <ul style="left:103px"><li>Categories</li><li>Search</li><li>Currency Converter</li></ul>
    <ul style="left:191px"><li>Sell New Item</li><li>Sell Bulk Items</li></ul>
    <ul style="left:273px"><li>Contact</li><li>Terms</li><li>Privacy</li><li>RSS</li></ul>
    <ul style="left:351px"><li>About</li><li>News</li><li>Feeds</li></ul>
    <div class="email">Enter Your Email...</div>
    <a class="sub" style="left:458px;background:#555">✉ Subscribe</a>
    <a class="sub" style="left:543px;background:var(--blue)">✉ Unsubscribe</a>
    <div class="social" aria-label="Social links"><i></i><i></i><i></i><i></i><i></i></div>
  </div>
  <div class="abs bottom">
    <div class="brand2"><i></i>Bidwell</div>
    <span class="copy">Copyright © 2014 . All Rights Reserved.</span>
    <span class="links">Vision &amp; Mission | Profile | Careers | Contact</span>
  </div>
</footer>

</body>
</html>
```